Business Card for Coastal Tundrabridge Advisory

We need a business card for Coastal Tundrabridge Advisory. The company website address is provided below. The company logo is attached. We provide specialized permafrost services to the mining, transportation, and oil & gas industries. The card should be prepared for:
Matthias Korhonen, PhD.
Coastal Tundrabridge Advisory
PO Box 418259
Quillwater, Alaska 99642
Direct: +1-907-555-0143
Email: mkorhonen@tundrabridgeadvisory.example
Website: www.coastaltundrabridgeadvisory.example

```html
<!DOCTYPE html>
<html lang="en">
<head>
<meta charset="utf-8">
<title>Coastal Tundrabridge Advisory — Business Card</title>
<link rel="stylesheet" href="https://fonts.googleapis.com/css2?family=Roboto+Condensed:ital,wght@0,400;0,700;1,700&display=swap">
<style>
  :root {
    --page: #ececec;
    --card-front: #ffffff;
    --card-back: #2f2f2f;
    --card-back-deep: #262626;
    --accent-grey: #808080;
    --ink: #1a1a1a;
    --ink-name: #3a3a3a;
    --logo-light: #f2f2f2;
  }
  * { box-sizing: border-box; margin: 0; padding: 0; }
  html, body {
    width: 1200px; height: 1199px; overflow: hidden;
    background: var(--page);
    font-family: "Roboto Condensed", "Arial Narrow", sans-serif;
  }
  .canvas { position: relative; width: 1200px; height: 1199px; }

  .card {
    position: absolute; left: 235px; width: 725px; height: 412px;
    border-radius: 28px; overflow: hidden;
  }
  .card--front { top: 155px; background: var(--card-front); }
  .card--back  { top: 650px; }

  /* front */
  .side-bar {
    position: absolute; left: 43px; top: 0; width: 28px; height: 228px;
    background: var(--accent-grey);
  }
  .icon-column { position: absolute; left: 43px; top: 235px; width: 28px; }
  .icon-cell {
    width: 28px; height: 24px; margin-bottom: 4px;
    background: var(--accent-grey);
    display: flex; align-items: center; justify-content: center;
  }
  .icon-cell:last-child { border-radius: 0 0 14px 14px; height: 28px; }
  .icon-cell svg { width: 12px; height: 12px; }

  .identity {
    position: absolute; right: 88px; top: 36px; text-align: right; color: var(--ink-name);
  }
  .identity__name { font-style: italic; font-weight: 700; font-size: 31px; line-height: 1; letter-spacing: -0.3px; }
  .identity__title { font-size: 14px; color: var(--ink); margin-top: 3px; }

  .person-tab {
    position: absolute; right: 0; top: 28px; width: 80px; height: 73px;
    background: var(--accent-grey); border-radius: 24px 0 0 24px;
    display: flex; align-items: center; justify-content: center;
  }
  .person-tab svg { width: 28px; height: 30px; }

  .address {
    position: absolute; left: 91px; top: 142px;
    font-size: 16px; line-height: 23px; color: var(--ink);
  }
  .contacts {
    position: absolute; left: 91px; top: 236px; list-style: none;
    font-size: 16px; line-height: 28px; color: var(--ink);
  }

  /* back */
  .back-field {
    position: absolute; inset: 0;
    background: linear-gradient(135deg, var(--card-back) 0%, var(--card-back-deep) 100%);
  }
  .company-name {
    position: absolute; left: 325px; top: 232px; width: 330px;
    color: var(--logo-light); font-weight: 700; font-size: 34px;
    line-height: 1.05; letter-spacing: 1px; text-transform: uppercase;
  }
</style>
</head>
<body>
<main class="canvas">

  <section class="card card--front" aria-label="Card front">
    <div class="side-bar"></div>

    <div class="identity">
      <h1 class="identity__name">Matthias Korhonen, PhD</h1>
      <p class="identity__title">Founder &amp; Director</p>
    </div>

    <div class="person-tab">
      <svg viewBox="0 0 28 30" aria-hidden="true">
        <circle cx="14" cy="8" r="7" fill="#fff"/>
        <path d="M1 30 v-5 a8 8 0 0 1 8-8 h10 a8 8 0 0 1 8 8 v5 z" fill="#fff"/>
      </svg>
    </div>

    <address class="address" style="font-style:normal">
      PO Box 418259<br>
      Quillwater, Alaska 99642
    </address>

    <div class="icon-column" aria-hidden="true">
      <div class="icon-cell">
        <svg viewBox="0 0 12 12"><path d="M2.5 1 L4.5 1 L5.3 3.6 L4 4.6 A6 6 0 0 0 7.4 8 L8.4 6.7 L11 7.5 L11 9.5 A1.5 1.5 0 0 1 9.5 11 A8.5 8.5 0 0 1 1 2.5 A1.5 1.5 0 0 1 2.5 1 Z" fill="#fff"/></svg>
      </div>
      <div class="icon-cell">
        <svg viewBox="0 0 12 12"><rect x="3.3" y="0.8" width="5.4" height="10.4" rx="1" fill="none" stroke="#fff" stroke-width="1.2"/></svg>
      </div>
      <div class="icon-cell">
        <svg viewBox="0 0 12 12"><rect x="1" y="2.5" width="10" height="7" rx="0.8" fill="#fff"/><path d="M1.5 3 L6 6.6 L10.5 3" fill="none" stroke="#808080" stroke-width="1"/></svg>
      </div>
      <div class="icon-cell">
        <svg viewBox="0 0 12 12"><circle cx="6" cy="6" r="5" fill="none" stroke="#fff" stroke-width="1.2"/><ellipse cx="6" cy="6" rx="2.2" ry="5" fill="none" stroke="#fff" stroke-width="1"/><line x1="1" y1="6" x2="11" y2="6" stroke="#fff" stroke-width="1"/></svg>
      </div>
    </div>

    <ul class="contacts">
      <li>+1-907-555-0143</li>
      <li>(907) 555 0178</li>
      <li>mkorhonen@tundrabridgeadvisory.example</li>
      <li>www.coastaltundrabridgeadvisory.example</li>
    </ul>
  </section>

  <section class="card card--back" aria-label="Card back">
    <div class="back-field" role="img" aria-label="Dark charcoal background with a repeating tone-on-tone company name pattern"></div>
    <p class="company-name">Coastal Tundrabridge Advisory</p>
  </section>

</main>
</body>
</html>
```